Brightwick Business Card

Looking for a business card design to incorporate our branding. We want to only use the colors listing in the Branding Package (attached).
Updates

Target Market(s)

People who need their phone or device fixed.

Industry/Entity Type

Electronics

Contact Information for Business Card

Please use:

Brightwick Gadget Clinic LLC
4810 E Harlow Ridge Rd
Suite 417
San Antonio, TX 78163

Marcus Delgrove, Store Manager

(210) 555-0147

Requirements
Must have
• Must include the colors that are contained within the Branding Package PDF file.

```html
<!DOCTYPE html>
<html lang="en">
<head>
<meta charset="utf-8">
<title>Brightwick Gadget Clinic Business Card</title>
<link href="https://fonts.googleapis.com/css2?family=Open+Sans:wght@300;400;600;700&display=swap" rel="stylesheet">
<style>
  :root {
    --backdrop: #3a3431;
    --card: #0e0e0e;
    --card-edge: #1c1c1c;
    --orange: #ff5500;
    --orange-deep: #f04e00;
    --white: #f4f4f4;
    --silver: #c9c9c9;
    --rule: #2a2a2a;
  }
  * { box-sizing: border-box; margin: 0; padding: 0; }
  html, body {
    width: 1200px; height: 900px; overflow: hidden;
    background: var(--backdrop);
    font-family: "Open Sans", Arial, sans-serif;
  }
  .stage {
    width: 1200px; height: 900px;
    display: flex; align-items: center; justify-content: center; gap: 60px;
  }
  .card {
    width: 525px; height: 300px;
    background: var(--card);
    border: 1px solid var(--card-edge);
    position: relative;
    box-shadow: 0 16px 34px rgba(0,0,0,.45);
  }
  /* front */
  .card-front { display: flex; }
  .brand-panel {
    width: 215px; height: 100%;
    display: flex; flex-direction: column; align-items: center; justify-content: center; gap: 14px;
    border-right: 1px solid var(--rule);
  }
  .brand-square {
    width: 140px; height: 140px; border-radius: 28px;
    background: var(--orange);
    border: 2px solid var(--orange-deep);
  }
  .brand-name {
    color: var(--orange); font-weight: 700; font-size: 19px; letter-spacing: .5px;
  }
  .contact-panel {
    flex: 1; padding: 62px 0 0 34px; color: var(--white);
  }
  .person-name { color: var(--orange); font-weight: 700; font-size: 19px; line-height: 1.1; }
  .person-role { font-size: 12px; margin-top: 2px; }
  .phone { display: flex; align-items: center; gap: 8px; font-size: 13px; margin-top: 20px; }
  .phone svg { width: 12px; height: 12px; fill: var(--orange); }
  .company { color: var(--orange); font-weight: 600; font-size: 13.5px; margin-top: 20px; }
  .address { font-size: 13.5px; line-height: 1.45; }
  /* back */
  .card-back { display: flex; align-items: center; justify-content: center; }
  .back-wordmark {
    color: var(--silver); font-weight: 300; font-size: 32px; letter-spacing: .5px;
  }
</style>
</head>
<body>
<main class="stage">
  <section class="card card-front">
    <div class="brand-panel">
      <div class="brand-square"></div>
      <div class="brand-name">Brightwick</div>
    </div>
    <div class="contact-panel">
      <div class="person-name">Marcus Delgrove</div>
      <div class="person-role">Store Manager</div>
      <div class="phone">
        <svg viewBox="0 0 24 24" aria-hidden="true"><path d="M6.6 10.8a15.1 15.1 0 0 0 6.6 6.6l2.2-2.2a1 1 0 0 1 1-.25 11.4 11.4 0 0 0 3.6.57 1 1 0 0 1 1 1V20a1 1 0 0 1-1 1A17 17 0 0 1 3 4a1 1 0 0 1 1-1h3.5a1 1 0 0 1 1 1c0 1.25.2 2.45.57 3.57a1 1 0 0 1-.25 1z"/></svg>
        <span>(210) 555-0147</span>
      </div>
      <div class="company">Brightwick Gadget Clinic LLC</div>
      <div class="address">4810 E Harlow Ridge Rd Suite<br>417 San Antonio, TX 78163</div>
    </div>
  </section>
  <section class="card card-back">
    <div class="back-wordmark">Brightwick Gadget Clinic</div>
  </section>
</main>
</body>
</html>
```